TALMORK

The business want a professional looking business card. We have a scetch we will add but want the extra upgrade, and would like more suggestions for variations of our business cards.

```html
<!DOCTYPE html>
<html lang="en">
<head>
<meta charset="utf-8">
<title>Talmork Business Card</title>
<link href="https://fonts.googleapis.com/css2?family=Montserrat:wght@400;500;700&display=swap" rel="stylesheet">
<style>
  :root {
    --stage: #1b1b1c;
    --card: #1d1d1e;
    --card-edge: #151516;
    --gold: #c9a246;
    --gold-light: #e6c778;
    --gold-dark: #9c7a2c;
    --white: #f4f4f4;
    --emboss: #2a2a2b;
  }
  * { margin: 0; padding: 0; box-sizing: border-box; }
  html, body { width: 1200px; height: 801px; overflow: hidden; }
  body {
    background: var(--stage);
    font-family: "Montserrat", sans-serif;
    position: relative;
  }
  .card {
    position: absolute;
    top: 252px;
    width: 520px;
    height: 297px;
    border-radius: 16px;
    background: linear-gradient(135deg, #232324 0%, var(--card) 55%, var(--card-edge) 100%);
    overflow: hidden;
    box-shadow: 0 18px 40px rgba(0,0,0,0.55);
  }
  .card-front { left: 60px; }
  .card-back { left: 620px; }

  .corner-tab {
    position: absolute;
    top: 0;
    right: 42px;
    width: 38px;
    height: 16px;
    background: linear-gradient(90deg, var(--gold-dark), var(--gold-light), var(--gold));
  }
  .holder {
    position: absolute;
    top: 34px;
    right: 58px;
    text-align: right;
  }
  .holder-name {
    color: var(--gold);
    font-weight: 700;
    font-size: 21px;
    letter-spacing: 0.2px;
  }
  .holder-title {
    color: var(--white);
    font-weight: 400;
    font-size: 15px;
    margin-top: 2px;
  }

  .brand {
    position: absolute;
    left: 40px;
    top: 108px;
    display: flex;
    align-items: center;
    gap: 10px;
  }
  .brand-dot {
    width: 12px;
    height: 12px;
    border-radius: 50%;
    background: var(--gold);
  }
  .brand-name {
    color: var(--gold);
    font-weight: 500;
    font-size: 24px;
    letter-spacing: 5px;
  }

  .contacts {
    position: absolute;
    left: 40px;
    bottom: 34px;
    list-style: none;
  }
  .contacts li {
    display: flex;
    align-items: center;
    gap: 10px;
    color: var(--white);
    font-size: 14px;
    line-height: 24px;
  }
  .contacts svg { width: 13px; height: 13px; fill: var(--gold); flex: none; }

  .edge-stripe {
    position: absolute;
    left: 0;
    bottom: 0;
    width: 100%;
    height: 10px;
    display: flex;
  }
  .edge-stripe .white-band { width: 48%; background: var(--white); }
  .edge-stripe .gold-band { width: 52%; background: linear-gradient(90deg, var(--gold-dark), var(--gold-light) 60%, var(--gold)); }

  .back-brand {
    position: absolute;
    inset: 0;
    display: flex;
    align-items: center;
    justify-content: center;
  }
  .back-brand-name {
    color: var(--emboss);
    font-weight: 500;
    font-size: 40px;
    letter-spacing: 9px;
    padding-left: 9px;
  }
</style>
</head>
<body>
  <section class="card card-front">
    <div class="corner-tab"></div>
    <div class="holder">
      <p class="holder-name">Lars Henrik Solvang</p>
      <p class="holder-title">CEO &amp; Founder</p>
    </div>
    <div class="brand">
      <span class="brand-dot"></span>
      <span class="brand-name">TALMORK</span>
    </div>
    <ul class="contacts">
      <li>
        <svg viewBox="0 0 24 24" aria-hidden="true"><path d="M6.6 10.8a15.1 15.1 0 0 0 6.6 6.6l2.2-2.2a1 1 0 0 1 1-.25 11.4 11.4 0 0 0 3.6.57 1 1 0 0 1 1 1V20a1 1 0 0 1-1 1A17 17 0 0 1 3 4a1 1 0 0 1 1-1h3.5a1 1 0 0 1 1 1c0 1.25.2 2.45.57 3.57a1 1 0 0 1-.25 1z"/></svg>
        004791234567
      </li>
      <li>
        <svg viewBox="0 0 24 24" aria-hidden="true"><path d="M2 5h20v14H2z M2 5l10 8 10-8" fill="none" stroke="#c9a246" stroke-width="2"/></svg>
        talmork.llc@mailpost.com
      </li>
      <li>
        <svg viewBox="0 0 24 24" aria-hidden="true"><path d="M12 2a10 10 0 1 0 0 20 10 10 0 0 0 0-20zm6.9 6h-3a15.7 15.7 0 0 0-1.4-3.6A8 8 0 0 1 18.9 8zM12 4a14 14 0 0 1 1.9 4h-3.8A14 14 0 0 1 12 4zM4.3 14a8 8 0 0 1 0-4h3.4a16.5 16.5 0 0 0 0 4zm.8 2h3a15.7 15.7 0 0 0 1.4 3.6A8 8 0 0 1 5.1 16zm3-8h-3a8 8 0 0 1 4.4-3.6A15.7 15.7 0 0 0 8.1 8zM12 20a14 14 0 0 1-1.9-4h3.8A14 14 0 0 1 12 20zm2.3-6H9.7a14.7 14.7 0 0 1 0-4h4.6a14.7 14.7 0 0 1 0 4zm.2 5.6a15.7 15.7 0 0 0 1.4-3.6h3a8 8 0 0 1-4.4 3.6zm1.8-5.6a16.5 16.5 0 0 0 0-4h3.4a8 8 0 0 1 0 4z"/></svg>
        www.talmork.llc
      </li>
    </ul>
    <div class="edge-stripe">
      <span class="white-band"></span>
      <span class="gold-band"></span>
    </div>
  </section>

  <section class="card card-back">
    <div class="back-brand">
      <span class="back-brand-name">TALMORK</span>
    </div>
  </section>
</body>
</html>
```